Business Card Design Project

Business Card
We are rebranding with a new logo
Industry/Entity Type
Business
Contact Information for Business Card
Dennis Morvale +61 487215963 dennis@quorv.com.au P.O. Box 872 Fernlow QLD 4309
Requirements
Must have
- Logo

```html
<!DOCTYPE html>
<html lang="en">
<head>
<meta charset="utf-8">
<title>Quorv International — Business Card</title>
<link rel="stylesheet" href="https://fonts.googleapis.com/css2?family=Montserrat:wght@400;500;600;700&display=swap">
<style>
  :root {
    --backdrop: #1d1d1f;
    --card-white: #ffffff;
    --brand-blue: #1d7aa0;
    --brand-blue-dark: #15607f;
    --ink: #1f1f22;
    --on-blue: #ffffff;
  }
  * { margin: 0; padding: 0; box-sizing: border-box; }
  html, body {
    width: 1200px;
    height: 837px;
    overflow: hidden;
    background: var(--backdrop);
    font-family: "Montserrat", sans-serif;
  }
  .canvas {
    position: relative;
    width: 1200px;
    height: 837px;
    display: flex;
    flex-direction: column;
    align-items: center;
    justify-content: center;
    gap: 44px;
  }
  .card {
    position: relative;
    width: 620px;
    height: 354px;
    border-radius: 22px;
    background: var(--card-white);
    overflow: hidden;
  }
  .card__band {
    position: absolute;
    inset: 0;
    width: 100%;
    height: 100%;
  }
  .brand {
    position: absolute;
    left: 0;
    right: 0;
    display: flex;
    align-items: center;
    justify-content: center;
    gap: 12px;
    color: var(--brand-blue);
  }
  .brand__dot {
    width: 22px;
    height: 22px;
    border-radius: 50%;
    background: var(--brand-blue);
  }
  .brand__name {
    font-weight: 700;
    font-size: 26px;
    letter-spacing: 0.14em;
    text-transform: uppercase;
  }
  .front .brand { top: 52px; }
  .front .person {
    position: absolute;
    top: 108px;
    left: 0;
    right: 0;
    text-align: center;
    font-size: 27px;
    font-weight: 600;
    color: var(--ink);
  }
  .contact-item {
    position: absolute;
    top: 192px;
    width: 200px;
    margin-left: -100px;
    display: flex;
    flex-direction: column;
    align-items: center;
    gap: 22px;
    color: var(--on-blue);
    font-size: 13px;
    font-weight: 500;
    letter-spacing: 0.02em;
  }
  .contact-item--phone { left: 100px; }
  .contact-item--mail { left: 310px; }
  .contact-item--pin { left: 510px; width: 240px; margin-left: -120px; }
  .contact-item svg { width: 46px; height: 46px; }
  .back .brand { top: 110px; }
  .back .brand__name { font-size: 30px; }
  .web {
    position: absolute;
    bottom: 62px;
    left: 0;
    right: 0;
    text-align: center;
    color: var(--on-blue);
    font-size: 15px;
    font-weight: 500;
    letter-spacing: 0.42em;
  }
</style>
</head>
<body>
<main class="canvas">

  <section class="card front" aria-label="Card front">
    <svg class="card__band" viewBox="0 0 620 354" preserveAspectRatio="none" aria-hidden="true">
      <path d="M0 216 C160 198 460 198 620 216 L620 354 L0 354 Z" fill="var(--brand-blue)"/>
      <path d="M0 216 C160 198 460 198 620 216 L620 222 C460 204 160 204 0 222 Z" fill="var(--brand-blue-dark)"/>
    </svg>

    <div class="brand">
      <span class="brand__dot"></span>
      <span class="brand__name">Quorv International</span>
    </div>
    <p class="person">Dennis Morvale</p>

    <div class="contact-item contact-item--phone">
      <svg viewBox="0 0 46 46" aria-hidden="true">
        <circle cx="23" cy="23" r="21" fill="var(--brand-blue)" stroke="#fff" stroke-width="3"/>
        <path d="M17 14 l4 0 l2 6 l-3 2 c1 3 3 5 6 6 l2 -3 l6 2 l0 4 c0 1 -1 2 -2 2 c-9 0 -17 -8 -17 -17 c0 -1 1 -2 2 -2 z" fill="#fff"/>
      </svg>
      <span>+61 487215963</span>
    </div>

    <div class="contact-item contact-item--mail">
      <svg viewBox="0 0 46 46" aria-hidden="true">
        <circle cx="23" cy="23" r="21" fill="var(--brand-blue)" stroke="#fff" stroke-width="3"/>
        <rect x="13" y="16" width="20" height="14" rx="1.5" fill="none" stroke="#fff" stroke-width="2"/>
        <path d="M13 17 L23 25 L33 17" fill="none" stroke="#fff" stroke-width="2"/>
      </svg>
      <span>dennis@quorv.com.au</span>
    </div>

    <div class="contact-item contact-item--pin">
      <svg viewBox="0 0 46 46" aria-hidden="true">
        <circle cx="23" cy="23" r="21" fill="var(--brand-blue)" stroke="#fff" stroke-width="3"/>
        <path d="M23 12 c-5 0 -8 4 -8 8 c0 6 8 14 8 14 c0 0 8 -8 8 -14 c0 -4 -3 -8 -8 -8 z" fill="#fff"/>
        <circle cx="23" cy="20" r="3" fill="var(--brand-blue)"/>
      </svg>
      <span>P.O. Box 872 Fernlow QLD 4309</span>
    </div>
  </section>

  <section class="card back" aria-label="Card back">
    <svg class="card__band" viewBox="0 0 620 354" preserveAspectRatio="none" aria-hidden="true">
      <path d="M0 240 C160 222 460 222 620 240 L620 354 L0 354 Z" fill="var(--brand-blue)"/>
    </svg>
    <div class="brand">
      <span class="brand__dot"></span>
      <span class="brand__name">Quorv International</span>
    </div>
    <p class="web">www.quorv.com.au</p>
  </section>

</main>
</body>
</html>
```